Business Card Design

Business Card for professional consulting firm working with large financial institutions.

Target Market(s)

Executive buyers

Industry/Entity Type

Banking

Contact Information for Business Card

Mild creativity wanted. Not boring, but do elaborate artwork.

Font styles to use
Serif
Sans Serif

Colors

Designer to choose colors to be used in the design.

Requirements
Must have
• Standard business card features - company name, individual name, telephone, website, email, locations.
Nice to have
• Two colors
Should not have
• too many colors, fancy printing, cartoons.

```html
<!DOCTYPE html>
<html lang="en">
<head>
<meta charset="utf-8">
<title>k7advisory – Business Card</title>
<link rel="stylesheet" href="https://fonts.googleapis.com/css2?family=Lato:wght@400;700&family=Open+Sans:wght@400&display=swap">
<style>
  :root {
    --backdrop: #e8e6e3;
    --card: #ffffff;
    --ink: #1b1b1b;
    --ink-soft: #2a2a2a;
    --brand: #1e1e1e;
  }
  * { box-sizing: border-box; margin: 0; padding: 0; }
  html, body {
    width: 1200px; height: 900px; overflow: hidden;
    background: var(--backdrop);
  }
  .card {
    position: absolute;
    left: 276px; top: 249px;
    width: 648px; height: 402px;
    background: var(--card);
    border-radius: 201px 0 0 201px;
    box-shadow: 0 10px 30px rgba(0,0,0,0.12);
  }
  .brand-name {
    position: absolute;
    left: 104px; top: 168px;
    font-family: "Lato", sans-serif;
    font-weight: 400;
    font-size: 42px;
    letter-spacing: 0.5px;
    color: var(--brand);
    white-space: nowrap;
  }
  .holder {
    position: absolute;
    right: 38px; top: 60px;
    text-align: right;
    font-family: "Lato", sans-serif;
    color: var(--ink);
    white-space: nowrap;
  }
  .holder-name { font-size: 24px; font-weight: 400; letter-spacing: 0.4px; line-height: 28px; }
  .holder-role { font-size: 17px; line-height: 22px; color: var(--ink-soft); }
  .contacts {
    position: absolute;
    right: 38px; top: 216px;
    list-style: none;
    font-family: "Open Sans", sans-serif;
    font-size: 16px;
    line-height: 24px;
    color: var(--ink);
    text-align: right;
    white-space: nowrap;
  }
  .contacts li { display: flex; justify-content: flex-end; align-items: center; gap: 3px; }
  .contacts svg { width: 14px; height: 14px; fill: var(--ink); }
  .address {
    position: absolute;
    right: 38px; top: 303px;
    font-family: "Open Sans", sans-serif;
    font-style: normal;
    font-size: 17px;
    line-height: 24px;
    text-align: right;
    color: var(--ink);
    white-space: nowrap;
  }
</style>
</head>
<body>
  <div class="card">
    <div class="brand-name">k7advisory</div>

    <div class="holder">
      <div class="holder-name">MARCUS HALE</div>
      <div class="holder-role">Managing Director</div>
    </div>

    <ul class="contacts">
      <li>044-987 650 412
        <svg viewBox="0 0 16 16" aria-hidden="true"><path d="M1 6c0-2 3-3 7-3s7 1 7 3v1h-3V5.5H4V7H1z"/><path d="M4 8h8l2 5H2z"/></svg>
      </li>
      <li>hello@k7advisory.com
        <svg viewBox="0 0 16 16" aria-hidden="true"><path d="M1 3h14v10H1z M2.5 4.5 8 9l5.5-4.5z" fill-rule="evenodd"/></svg>
      </li>
      <li>www.k7advisory.com
        <svg viewBox="0 0 16 16" aria-hidden="true"><circle cx="8" cy="8" r="7"/><path d="M5 5c1 0 2 1 1 2s-2 1-1 3M10 3c-1 1 0 2 1 2s2 1 1 3-2 2-1 4" stroke="#fff" stroke-width="1.2" fill="none"/></svg>
      </li>
    </ul>

    <address class="address">
      48 Harbour Lane, Suite 12<br>
      Northbridge, 204518
    </address>
  </div>
</body>
</html>
```